Valdo Capital

We need a corporate style website design for a new company based in Shenzhen's Qianhai Special Economic Development Zone, China. We provide a range of financial services to large international investment companies. Typically these companies invest over 5 million RMB. The company is part of a group that consists of NorthKilns, ValdoTrusts and ValdoEquity. Our location and gateway into Qianhai Special Economic Zone is our core advantage. We would like to see designs that Do Not use purple and orange. The website design should be similar to other websites in this family but different enough to give it a unique style (See attached website links for reference). The final design should communicate financial safety and growth. This website will act partly as a business chamber with connections to the government so we would like it to be diplomatic in style.

www.northkilns.example
www.valdotrusts.example

*Nevegation Bar
Should including Homepage, Financial Product, Team, News.
Could refer to www.valdotrusts.example

*Contact Details

Miss Lan
Address:E 728, North Block, KMO Centre, East Sector, Shenzhen Bright Science Campus
Telephone: +86 0755 63920417
Cellphone: +86 13957280316

* Social Media
Should be grouped like:
1. Weibo QRcode+ Weibo
2. Facebook, Twitter, Linkedin.

Industry/Entity Type

Investment

```html
<!DOCTYPE html>
<html lang="en">
<head>
<meta charset="utf-8">
<title>Valdo Capital</title>
<link href="https://fonts.googleapis.com/css2?family=Open+Sans:wght@300;400;600;700&family=PT+Sans+Narrow:wght@400;700&display=swap" rel="stylesheet">
<style>
  :root{
    --blue:#1e9ad6;
    --navy:#1d3b5c;
    --ink:#3a3a3a;
    --muted:#7d7d7d;
    --line:#e1e1e1;
    --page:#f5f6f7;
    --white:#ffffff;
    --red:#d9363e;
    --footer:#2f3133;
    --footer-deep:#222325;
    --footer-text:#a9adb1;
  }
  *{box-sizing:border-box;margin:0;padding:0}
  html,body{width:828px;height:1200px;overflow:hidden}
  body{position:relative;background:var(--page);font-family:"Open Sans",Arial,sans-serif;color:var(--ink)}
  a{color:inherit;text-decoration:none}

  .site-header{position:absolute;left:0;top:0;width:828px;height:97px;background:var(--white)}
  .brand{position:absolute;left:72px;top:26px;display:flex;align-items:center;gap:10px}
  .brand-mark{width:34px;height:34px;background:var(--navy)}
  .brand-name{font-size:22px;font-weight:700;color:var(--navy);letter-spacing:.3px}
  .social-top{position:absolute;right:72px;top:14px;display:flex;gap:6px}
  .social-top span{width:19px;height:19px;border-radius:50%;background:var(--red)}
  .main-nav{position:absolute;left:360px;top:50px;display:flex;gap:2px}
  .main-nav a{font-size:11px;font-weight:600;color:var(--ink);padding:8px 14px}
  .main-nav a.is-active{color:var(--blue);border-bottom:2px solid var(--blue)}

  .hero{position:absolute;left:0;top:97px;width:828px;height:291px;
    background:linear-gradient(115deg,#ffffff 0%,#e9f1f7 35%,#c9dcea 62%,#8fb5d4 82%,#4f7fae 100%)}
  .hero-band{position:absolute;left:72px;top:96px;width:480px;height:64px;background:rgba(30,154,214,.88);padding:8px 16px}
  .hero-band h1{font-family:"PT Sans Narrow",Arial,sans-serif;font-weight:400;font-size:30px;line-height:32px;color:var(--white)}
  .hero-band p{font-size:9px;color:#e6f4fb;margin-top:4px}

  .features{position:absolute;left:72px;top:400px;display:flex;gap:10px}
  .card{width:160px;height:256px;background:var(--white)}
  .card-label{height:24px;background:var(--blue);color:var(--white);font-size:10px;font-weight:600;padding:6px 10px}
  .card-media{height:88px}
  .media-meeting{background:linear-gradient(135deg,#8fa3b6,#d7dee4 55%,#6d7f90)}
  .media-chart{background:linear-gradient(135deg,#eef2f5,#b8c6d2 60%,#5d7389)}
  .media-office{background:linear-gradient(135deg,#3f6687,#9db8cf 60%,#dfe8ef)}
  .card-body{padding:10px}
  .card-body h3{font-size:10px;font-weight:600;color:var(--blue);margin-bottom:5px}
  .card-body p{font-size:8.5px;line-height:12.5px;color:var(--muted)}
  .more{display:block;font-size:8.5px;color:var(--blue);margin-top:6px}

  .ambition{position:absolute;left:593px;top:402px;width:166px}
  .ambition h2{font-family:"PT Sans Narrow",Arial,sans-serif;font-weight:400;font-size:21px;line-height:23px;color:var(--blue);margin-bottom:10px}
  .ambition p{font-size:8.5px;line-height:13px;color:var(--muted);margin-bottom:9px}

  .divider{position:absolute;left:72px;top:670px;width:687px;height:2px;background:var(--blue)}

  .columns{position:absolute;left:72px;top:682px;width:687px;display:flex;gap:22px}
  .col{width:214px}
  .col h4{font-size:11px;font-weight:600;color:var(--blue);padding-bottom:7px;border-bottom:1px solid var(--line);margin-bottom:12px}
  .news-item{display:flex;gap:10px;margin-bottom:16px}
  .news-date{width:28px;text-align:center;flex:none}
  .news-date b{display:block;font-size:15px;font-weight:700;color:var(--ink)}
  .news-date small{font-size:8px;color:var(--muted)}
  .news-item h5{font-size:10px;font-weight:600;margin-bottom:4px}
  .news-item p,.read p{font-size:8.5px;line-height:12.5px;color:var(--muted)}
  .read{display:flex;gap:10px;margin-bottom:16px}
  .read-thumb{width:66px;height:52px;flex:none;background:linear-gradient(135deg,#5d7b97,#c6d5e2)}
  .quote{font-size:8.5px;line-height:13px;color:var(--muted);font-style:italic;background:var(--white);padding:10px;border-left:3px solid var(--blue)}
  .quote-author{font-size:9px;font-weight:600;margin-top:9px}
  .quote-author span{font-weight:400;color:var(--muted)}

  .site-footer{position:absolute;left:0;top:945px;width:828px;height:195px;background:var(--footer);color:var(--footer-text)}
  .footer-cols{position:absolute;left:72px;top:24px;width:687px;display:flex;gap:22px}
  .footer-cols section{width:154px}
  .footer-cols h6{font-size:10.5px;font-weight:600;color:var(--white);margin-bottom:12px}
  .footer-cols p{font-size:8.5px;line-height:13px;margin-bottom:9px}
  .post-date{display:block;font-size:8px;color:#7f858a}
  .email-field{width:150px;height:24px;border:1px solid #55595d;background:#3a3c3f;font-size:8.5px;color:#8b9095;padding:6px 8px;margin-bottom:9px}
  .btn-subscribe{display:inline-block;background:var(--blue);color:var(--white);font-size:9px;font-weight:600;padding:6px 14px}
  .social-foot{display:flex;gap:6px}
  .social-foot span{width:20px;height:20px;border-radius:50%;background:#5a5e62}

  .bottom-bar{position:absolute;left:0;top:1140px;width:828px;height:60px;background:var(--footer-deep);text-align:center;padding-top:14px;font-size:8.5px;color:#7f858a}
</style>
</head>
<body>

<header class="site-header">
  <div class="brand"><span class="brand-mark"></span><span class="brand-name">Valdo Capital</span></div>
  <div class="social-top" aria-label="Social links">
    <span></span><span></span><span></span><span></span><span></span>
  </div>
  <nav class="main-nav">
    <a href="#" class="is-active">Home</a>
    <a href="#">Financial Product</a>
    <a href="#">Team</a>
    <a href="#">News</a>
  </nav>
</header>

<section class="hero" role="img" aria-label="Photo of financial charts and a hand working with a pen on paper reports">
  <div class="hero-band">
    <h1>It feels different to work here</h1>
    <p>Our people and culture set us apart, bringing clear values to every client we serve.</p>
  </div>
</section>

<div class="features">
  <article class="card">
    <div class="card-label">About us</div>
    <div class="card-media media-meeting" role="img" aria-label="Photo of a business meeting"></div>
    <div class="card-body">
      <h3>Global Private Equity Report 2014</h3>
      <p>A focused review of cross-border capital flows and the year ahead.</p>
      <a class="more" href="#">Learn More »</a>
    </div>
  </article>
  <article class="card">
    <div class="card-label">Financial Product</div>
    <div class="card-media media-chart" role="img" aria-label="Photo of printed financial charts"></div>
    <div class="card-body">
      <h3>Responsibility</h3>
      <p>The principles that guide prudent, steady growth for every partner.</p>
      <a class="more" href="#">Learn More »</a>
    </div>
  </article>
  <article class="card">
    <div class="card-label">What We Do</div>
    <div class="card-media media-office" role="img" aria-label="Photo of a modern office building"></div>
    <div class="card-body">
      <h3>A career in Valdo</h3>
      <p>Join a team shaping trusted capital links into Qianhai.</p>
      <a class="more" href="#">Learn More »</a>
    </div>
  </article>
</div>

<aside class="ambition">
  <h2>Shared Ambition True Results</h2>
  <p>We are based in Shenzhen's Qianhai Special Economic Development Zone, China.</p>
  <p>We provide a range of financial services to large international investment companies.</p>
  <p>Typically these companies invest over 5 million RMB. The company is part of a group.</p>
  <a class="more" href="#">Learn More »</a>
</aside>

<div class="divider"></div>

<div class="columns">
  <section class="col">
    <h4>Latest News</h4>
    <div class="news-item">
      <div class="news-date"><b>24</b><small>Jul</small></div>
      <div>
        <h5>Transforming a leading polymers</h5>
        <p>A step-by-step look at how a regional manufacturer refinanced its growth plan.</p>
      </div>
    </div>
    <div class="news-item">
      <div class="news-date"><b>24</b><small>Jul</small></div>
      <div>
        <h5>Strategic M&amp;A approach cranks up savings</h5>
        <p>How careful deal selection lowered costs and opened new markets for a client.</p>
      </div>
    </div>
  </section>
  <section class="col">
    <h4>Top Reads</h4>
    <div class="read">
      <div class="read-thumb" role="img" aria-label="Photo of a business report"></div>
      <p>A practical guide to fund structures for new investors entering the Qianhai zone this year.</p>
    </div>
    <div class="read">
      <div class="read-thumb" role="img" aria-label="Photo of a boardroom"></div>
      <p>Five questions every board should ask before committing capital across borders.</p>
    </div>
  </section>
  <section class="col">
    <h4>Testimonials</h4>
    <div class="quote">Valdo guided our entry into Qianhai with patience and care. Their team understood both the rules and our goals, and every step felt secure.</div>
    <div class="quote-author">Helen Zhou <span>CEO, Harbor Group</span></div>
    <a class="more" href="#">View All Testimonials</a>
  </section>
</div>

<footer class="site-footer">
  <div class="footer-cols">
    <section>
      <h6>CONTACT INFO</h6>
      <p>Our team is ready to help you plan your next investment in Qianhai.</p>
      <p>Harbour Place (00) 5550-0199</p>
      <p>hello@valdocapital.example</p>
    </section>
    <section>
      <h6>Recent Blog Posts</h6>
      <p>New guidance on cross-border fund registration released.<span class="post-date">July 7, 2014</span></p>
      <p>Quarterly outlook: steady growth across regional markets.<span class="post-date">July 7, 2014</span></p>
    </section>
    <section>
      <h6>Subscribe to our Newsletter</h6>
      <div class="email-field">Enter Your Email</div>
      <a class="btn-subscribe" href="#">Subscribe</a>
    </section>
    <section>
      <h6>Follow Us</h6>
      <div class="social-foot" aria-label="Social links">
        <span></span><span></span><span></span>
      </div>
    </section>
  </div>
</footer>

<div class="bottom-bar">© Copyright 2014, Valdo Capital. All Rights Reserved</div>

</body>
</html>
```